Ferntrail Electric Rides NZ

We are an Electric Mountain bike tour company in New Zealand. We will be offering bike rental and guided tours around the Nelson region in New Zealand. I want our website to represent both Mountain biking and New Zealand with the colours layout and features. We want tabs for the following:
-1 about us
-2 what we offer
-3 bookings/contact
Under the about us tab will be who we are as a a company. I want the ability to add videos to each of these tabs as we move foward with videos of the tracks we will be riding. I want the website to be editable so I can add and remove videos/photos myself. Also "our bikes" will be under this tab.
Under the what we offer tab will be
-1 bike rental and pricing
-2 guided tours and pricing
-3 recommended package deals.
I want to able to put the tracks under the guided tours tab and select beginner/ intermediate/advanced and have the tracks in each of the following to match the rider level. Also to be able to have a small video of the track would be great in this section.
Bookings and contact tab
(Further information for this tab to be updated soon)
Coded - Design and coding required
1 page
- Silver ferns, kiwi, mountains

```html
<!DOCTYPE html>
<html lang="en">
<head>
<meta charset="utf-8">
<title>Ferntrail Electric Rides NZ</title>
<link href="https://fonts.googleapis.com/css2?family=Lato:wght@400;700;900&display=swap" rel="stylesheet">
<style>
:root{
  --ink:#111;
  --text:#333;
  --muted:#9a9a9a;
  --white:#fff;
  --band:#e6e6e4;
  --dark:#1d2126;
  --footer:#050505;
  --footer-bar:#2b2b2b;
  --field:#111;
  --accent-red:#c0201e;
}
*{box-sizing:border-box;margin:0;padding:0}
html,body{width:1200px;height:4036px;overflow:hidden}
body{font-family:'Lato',sans-serif;color:var(--text);background:var(--white);position:relative}
section,header,footer{position:absolute;left:0;width:1200px}
.abs{position:absolute}
.center{text-align:center;left:0;width:1200px}
h2{font-weight:700;font-size:30px;color:var(--ink)}
h2 span{color:var(--muted);font-weight:400}
p{font-size:15.5px;line-height:1.6}

/* header */
.site-header{top:0;height:140px;background:var(--white)}
.brand{left:80px;top:40px;display:flex;align-items:center;gap:12px;font-weight:900;font-size:26px;color:var(--ink)}
.brand i{width:44px;height:44px;border-radius:50%;background:var(--ink);display:block}
.phone{left:858px;top:39px;font-size:16px;color:var(--ink);display:flex;gap:8px;align-items:center}
.socials{left:1028px;top:39px;display:flex;gap:5px}
.socials i{display:block;width:19px;height:19px;background:var(--ink)}
.main-nav{top:82px;left:738px;display:flex;gap:52px;font-size:14.5px;font-weight:700;color:var(--ink)}
.main-nav .current{color:var(--muted);font-weight:400}

/* hero */
.hero{top:140px;height:573px;background:linear-gradient(180deg,#6b7177 0%,#8d8f86 40%,#5e5a3a 70%,#3b3726 100%)}
.hero h1{top:222px;font-size:60px;font-weight:900;color:var(--white);letter-spacing:1px}
.hero .tag{top:296px;font-size:27px;color:var(--white)}
.chev{width:26px;height:44px}

/* buttons */
.btn{display:inline-flex;align-items:center;gap:10px;background:var(--ink);color:var(--white);font-size:12.5px;font-weight:700;height:32px;padding:0 8px 0 18px;border-radius:16px}
.btn i{width:20px;height:20px;border-radius:50%;background:var(--white);display:flex;align-items:center;justify-content:center}

/* about */
.about{top:713px;height:692px}
.about h2{top:50px}
.about .intro{top:100px;color:var(--text)}
.photo{position:absolute;border-radius:2px}
.about .lead{top:370px;left:170px;width:860px;text-align:center;color:var(--text)}

/* bike */
.our-bike{top:1405px;height:325px;background:var(--band)}
.bike-badge{left:508px;top:-83px;width:184px;height:184px;border-radius:50%;background:var(--ink);border:14px solid var(--ink);box-shadow:inset 0 0 0 22px var(--white)}
.our-bike h2{top:128px}
.our-bike .lead{top:176px;left:150px;width:900px;text-align:center;color:var(--ink)}

/* offer */
.offer{top:1730px;height:718px;background:linear-gradient(180deg,#2b3036 0%,#1c1f22 55%,#262a2c 100%)}
.offer h2{top:58px;color:var(--white)}
.offer h2 span{color:var(--white)}
.offer .intro{top:112px;color:var(--white)}
.card{position:absolute;background:var(--white);width:279px;box-shadow:0 2px 8px rgba(0,0,0,.35)}
.card .img{height:237px}
.card h3{font-size:15px;font-weight:700;color:var(--ink);text-align:center;margin-top:30px}
.card p{font-size:12.5px;line-height:1.5;text-align:center;padding:6px 26px 0}
.card .btn{position:absolute;left:50%;transform:translateX(-50%);bottom:-16px}
.offer .card{top:226px;height:412px}
.blog .card{top:142px;height:410px}
.blog .card .img{height:250px}
.blog .card h3{margin-top:22px}
.blog .card .date{font-size:12.5px;text-align:center;margin-top:2px}

/* testimonials / video */
.stories{top:2448px;height:490px}
.quote-box{left:126px;top:135px;width:399px;height:247px;border:2px solid #9b9b9b;border-radius:6px;padding:58px 22px 0 40px;font-size:12.5px;line-height:1.45}
.quote-box:before{content:"\201C";position:absolute;left:20px;top:52px;font-size:30px;font-weight:900;color:var(--ink)}
.avatar{left:145px;top:87px;width:96px;height:96px;border-radius:50%;background:linear-gradient(160deg,#c9b19a,#6f8597);border:4px solid var(--white);box-shadow:0 0 0 2px #bbb}
.author{left:430px;top:410px;font-size:14px;color:var(--ink)}
.divider{left:603px;top:40px;width:1px;height:345px;background:#c8c8c8}
.video{left:672px;top:143px;width:399px;height:234px;background:linear-gradient(180deg,#6f8aa3,#dfe6ee 55%,#2d3a47)}
.play{left:175px;top:92px;width:48px;height:48px;border-radius:50%;background:var(--white)}
.controls{left:0;bottom:0;width:399px;height:30px;background:rgba(0,0,0,.85)}
.progress{left:60px;top:13px;width:320px;height:4px;background:#666}
.progress b{display:block;width:110px;height:4px;background:var(--accent-red)}

/* blog */
.blog{top:2938px;height:645px;background:linear-gradient(180deg,#b9b9b9 0%,#8f8f8f 45%,#d8d8d8 100%)}
.blog h2{top:58px}

/* footer */
.site-footer{top:3583px;height:393px;background:var(--footer);color:var(--white)}
.site-footer h4{font-size:18px;font-weight:700;letter-spacing:.5px}
.field{position:absolute;border:1.5px solid #8a8a8a;background:var(--field);color:var(--white);font-size:12.5px;padding:8px 10px;height:35px}
.submit{left:129px;top:310px;width:119px;height:29px;background:#a4a4a4;color:var(--white);font-size:13px;text-align:center;line-height:29px}
.contact-list{left:656px;top:104px;font-size:12.5px;line-height:1.6}
.quick{left:880px;top:104px;font-size:13px;line-height:1.9;list-style:none}
.quick li:before{content:"\203A";margin-right:12px}
.foot-socials{left:656px;top:308px;display:flex;gap:5px}
.foot-socials i{display:block;width:20px;height:20px;background:var(--white)}
.call-num{left:880px;top:303px;font-size:26px;font-weight:400}
.legal{top:3976px;height:60px;background:var(--footer-bar);color:#bdbdbd;font-size:13px;text-align:center;line-height:60px}
</style>
</head>
<body>

<header class="site-header">
  <div class="abs brand"><i></i>FERNTRAIL</div>
  <div class="abs phone">
    <svg width="16" height="16" viewBox="0 0 24 24"><path fill="#111" d="M6.6 10.8a15 15 0 0 0 6.6 6.6l2.2-2.2a1 1 0 0 1 1-.25 11.4 11.4 0 0 0 3.6.57 1 1 0 0 1 1 1V20a1 1 0 0 1-1 1A17 17 0 0 1 3 4a1 1 0 0 1 1-1h3.5a1 1 0 0 1 1 1c0 1.25.2 2.45.57 3.57a1 1 0 0 1-.25 1z"/></svg>
    (416) 555 0199
  </div>
  <div class="abs socials"><i></i><i></i><i></i><i></i></div>
  <nav class="abs main-nav"><span class="current">About us</span><span>What we offer</span><span>Bookings/Contact</span></nav>
</header>

<section class="hero" role="img" aria-label="Riders on electric mountain bikes crossing a grassy hilltop at dusk">
  <svg class="abs chev" style="left:52px;top:264px" viewBox="0 0 26 44"><path d="M22 4 4 22l18 18" fill="none" stroke="#fff" stroke-width="4"/></svg>
  <svg class="abs chev" style="right:52px;top:264px" viewBox="0 0 26 44"><path d="m4 4 18 18L4 40" fill="none" stroke="#fff" stroke-width="4"/></svg>
  <h1 class="abs center">FERNTRAIL</h1>
  <div class="abs center tag">Ferntrail Electric Rides NZ</div>
</section>

<section class="about">
  <h2 class="abs center">About <span>Us</span></h2>
  <p class="abs center intro">We are an Electric Mountain bike tour company in New Zealand.<br>We will be offering bike rental and guided tours around the Nelson region in New Zealand.</p>
  <div class="photo" role="img" aria-label="Rider on a mountain trail above a valley" style="left:153px;top:169px;width:285px;height:170px;background:linear-gradient(160deg,#9fb4c6,#8a7a5e 60%,#5d4e3a)"></div>
  <div class="photo" role="img" aria-label="Two riders with helmets on a sunny track" style="left:458px;top:169px;width:285px;height:170px;background:linear-gradient(160deg,#d8c08a,#9a8d5a 55%,#6b6a4a)"></div>
  <div class="photo" role="img" aria-label="Riders on a forest single track" style="left:759px;top:169px;width:285px;height:170px;background:linear-gradient(160deg,#a7c27a,#5f8a3d 55%,#3a5a2a)"></div>
  <p class="abs lead">Lorem ipsum dolor sit amet, consectetuer adipiscing elit. Aenean commodo ligula eget dolor. Aenean massa. Cum sociis natoque penatibus et magnis dis parturient montes, nascetur ridiculus mus. Donec quam felis, ultricies nec, pellentesque eu, pretium quis, sem. Nulla consequat massa quis enim. Donec pede justo, fringilla vel, aliquet nec, vulputate eget, arcu.In enim justo, rhoncus ut, imperdiet a, venenatis vitae, justo. Nullam dictum felis eu pede mollis pretium.Integer tincidunt. Cras dapibus. Vivamus elementum semper nisi.</p>
  <div class="abs center" style="top:522px"><span class="btn">Read More <i><svg width="9" height="9" viewBox="0 0 10 10"><path d="m3 1 4 4-4 4" fill="none" stroke="#111" stroke-width="2"/></svg></i></span></div>
</section>

<section class="our-bike">
  <div class="abs bike-badge" role="img" aria-label="Electric mountain bike emblem"></div>
  <h2 class="abs center">Our Bike</h2>
  <p class="abs lead">Lorem ipsum dolor sit amet, consectetuer adipiscing elit. Aenean commodo ligula eget dolor. Aenean massa. Cum sociis natoque penatibus et magnis dis parturient montes, nascetur ridiculus mus. Donec quam felis, ultricies nec, pellentesque eu</p>
  <div class="abs center" style="top:256px"><span class="btn">Read More <i><svg width="9" height="9" viewBox="0 0 10 10"><path d="m3 1 4 4-4 4" fill="none" stroke="#111" stroke-width="2"/></svg></i></span></div>
</section>

<section class="offer">
  <h2 class="abs center">What <span>we Offer</span></h2>
  <p class="abs center intro">Lorem ipsum dolor sit amet, consectetuer adipiscing elit. Aenean commodo ligula eget dolor. Aenean massa.<br>Cum sociis natoque penatibus et magnis dis parturient montes, nascetur ridiculus mus.</p>
  <svg class="abs chev" style="left:52px;top:404px" viewBox="0 0 26 44"><path d="M22 4 4 22l18 18" fill="none" stroke="#fff" stroke-width="4"/></svg>
  <svg class="abs chev" style="right:52px;top:404px" viewBox="0 0 26 44"><path d="m4 4 18 18L4 40" fill="none" stroke="#fff" stroke-width="4"/></svg>
  <article class="card" style="left:143px">
    <div class="img" role="img" aria-label="Mountain bike parked above a lake and snowy peaks" style="background:linear-gradient(180deg,#4f7fb0,#b8c9d6 45%,#6f5b3f)"></div>
    <h3>Bike rental &amp; pricing</h3>
    <p>Lorem ipsum dolor sit amet, consectetuer adipiscing elit. Aenean commodo ligula eget dolor. Aenean massa. Cum sociis natoque penatibus et magnis dis parturient montes, nascetur ridiculus mus.</p>
    <span class="btn">Read More <i><svg width="9" height="9" viewBox="0 0 10 10"><path d="m3 1 4 4-4 4" fill="none" stroke="#111" stroke-width="2"/></svg></i></span>
  </article>
  <article class="card" style="left:458px">
    <div class="img" role="img" aria-label="Two riders standing with their bikes" style="background:linear-gradient(180deg,#c7d3dc,#b59c72 55%,#5a5448)"></div>
    <h3>Guided tours &amp; pricing</h3>
    <p>Lorem ipsum dolor sit amet, consectetuer adipiscing elit. Aenean commodo ligula eget dolor. Aenean massa. Cum sociis natoque penatibus et magnis dis parturient montes, nascetur ridiculus mus.</p>
    <span class="btn">Read More <i><svg width="9" height="9" viewBox="0 0 10 10"><path d="m3 1 4 4-4 4" fill="none" stroke="#111" stroke-width="2"/></svg></i></span>
  </article>
  <article class="card" style="left:767px">
    <div class="img" role="img" aria-label="Riders on a green forest trail" style="background:linear-gradient(180deg,#b7cf8b,#5f8a3d 55%,#3a5a2a)"></div>
    <h3>Recommended package deals</h3>
    <p>Lorem ipsum dolor sit amet, consectetuer adipiscing elit. Aenean commodo ligula eget dolor. Aenean massa. Cum sociis natoque penatibus et magnis dis parturient montes, nascetur ridiculus mus.</p>
    <span class="btn">Read More <i><svg width="9" height="9" viewBox="0 0 10 10"><path d="m3 1 4 4-4 4" fill="none" stroke="#111" stroke-width="2"/></svg></i></span>
  </article>
</section>

<section class="stories">
  <h2 class="abs" style="left:282px;top:72px;font-size:27px">Client <span>Testimonials</span></h2>
  <div class="abs quote-box">Lorem ipsum dolor sit amet, consectetur adipiscing elit. Quid autem habent admirationis, cum prope accesseris? An hoc usque quaque, aliter in vita? Nam igit ur de imprebo, sed de callido improbo quaerimus, qualis Duo Reges: constructio interrete. Quae hic ronesto quo quam honestius nec turpi turpius. Tria genera bonorum. Quid iudicant sensus? Quae qui non vident, nihil umquam magnum ac cognitione dignum amaverunt. Dicet pro me ipsa virtus nec dubitabit.</div>
  <div class="abs avatar" role="img" aria-label="Client portrait"></div>
  <div class="abs author">Harper.L.K.</div>
  <div class="abs divider"></div>
  <h2 class="abs" style="left:672px;top:72px;font-size:27px">Featured <span>Video</span></h2>
  <div class="abs video" role="img" aria-label="Video still of a rider on a snowy downhill trail">
    <div class="abs play"><svg width="48" height="48" viewBox="0 0 48 48"><path d="M19 15v18l15-9z" fill="#111"/></svg></div>
    <div class="abs controls">
      <svg class="abs" style="left:12px;top:9px" width="30" height="12" viewBox="0 0 30 12"><path d="M0 0v12l9-6z" fill="#fff"/><path d="M17 0h3v12h-3zM23 0h3v12h-3z" fill="#fff"/></svg>
      <div class="abs progress"><b></b></div>
    </div>
  </div>
</section>

<section class="blog">
  <h2 class="abs center">Latest Blog</h2>
  <svg class="abs chev" style="left:52px;top:310px" viewBox="0 0 26 44"><path d="M22 4 4 22l18 18" fill="none" stroke="#fff" stroke-width="4"/></svg>
  <svg class="abs chev" style="right:52px;top:310px" viewBox="0 0 26 44"><path d="m4 4 18 18L4 40" fill="none" stroke="#fff" stroke-width="4"/></svg>
  <article class="card" style="left:143px">
    <div class="img" role="img" aria-label="Mountain bike above a lake and snowy peaks" style="background:linear-gradient(180deg,#4f7fb0,#b8c9d6 45%,#6f5b3f)"></div>
    <h3>Lorem ipsum dolor sit amet</h3>
    <div class="date">October 25, 2017.</div>
    <p>Lorem ipsum dolor sit amet, consectetuer adipiscing elit. Aenean commodo ligula eget dolor. Aenean massa.</p>
    <span class="btn">Read More <i><svg width="9" height="9" viewBox="0 0 10 10"><path d="m3 1 4 4-4 4" fill="none" stroke="#111" stroke-width="2"/></svg></i></span>
  </article>
  <article class="card" style="left:458px">
    <div class="img" role="img" aria-label="Two riders standing with their bikes" style="background:linear-gradient(180deg,#c7d3dc,#b59c72 55%,#5a5448)"></div>
    <h3>Lorem ipsum dolor sit amet</h3>
    <div class="date">October 25, 2017.</div>
    <p>Lorem ipsum dolor sit amet, consectetuer adipiscing elit. Aenean commodo ligula eget dolor. Aenean massa.</p>
    <span class="btn">Read More <i><svg width="9" height="9" viewBox="0 0 10 10"><path d="m3 1 4 4-4 4" fill="none" stroke="#111" stroke-width="2"/></svg></i></span>
  </article>
  <article class="card" style="left:772px">
    <div class="img" role="img" aria-label="Riders on a green forest trail" style="background:linear-gradient(180deg,#b7cf8b,#5f8a3d 55%,#3a5a2a)"></div>
    <h3>Lorem ipsum dolor sit amet</h3>
    <div class="date">October 25, 2017.</div>
    <p>Lorem ipsum dolor sit amet, consectetuer adipiscing elit. Aenean commodo ligula eget dolor. Aenean massa.</p>
    <span class="btn">Read More <i><svg width="9" height="9" viewBox="0 0 10 10"><path d="m3 1 4 4-4 4" fill="none" stroke="#111" stroke-width="2"/></svg></i></span>
  </article>
</section>

<footer class="site-footer">
  <h4 class="abs" style="left:129px;top:58px">Booking</h4>
  <div class="field" style="left:129px;top:105px;width:213px">First Name:</div>
  <div class="field" style="left:352px;top:105px;width:213px">LastName :</div>
  <div class="field" style="left:129px;top:146px;width:213px">Phone No :</div>
  <div class="field" style="left:352px;top:146px;width:213px">Email Address :</div>
  <div class="field" style="left:129px;top:189px;width:436px;height:88px">Message :</div>
  <div class="abs submit">Submit</div>

  <h4 class="abs" style="left:656px;top:58px">Contact</h4>
  <div class="abs contact-list">
    42 Harbour Lane<br>Nelson 7010<br>
    <span style="display:block;margin-top:8px">&#9990; 416-555-0199</span>
    <span>&#9993; hello@ferntrail.example</span><br>
    <span>&#9679; www.ferntrail.example</span>
  </div>
  <h4 class="abs" style="left:656px;top:272px;font-size:15px">FOLLOW US ON</h4>
  <div class="abs foot-socials"><i></i><i></i><i></i><i></i></div>

  <h4 class="abs" style="left:880px;top:58px">Quick Links</h4>
  <ul class="abs quick"><li>About us</li><li>What we offer</li><li>Bookings/Contact</li></ul>
  <h4 class="abs" style="left:880px;top:272px;font-size:15px">CALL US ON</h4>
  <div class="abs call-num">(416) 555 0199</div>
</footer>
<div class="abs center legal">© 2017 ferntrail &nbsp;|&nbsp; Privacy Policy &nbsp;|&nbsp; User Agreement</div>

</body>
</html>
```